Create a memorable Stationary for Security Software Company

Velbrantix is the worldwide leader in securing the Internet. Making Internet communications and critical data secure, reliable and available everywhere has been and continues to be our ongoing vision. We are committed to staying focused on real customer needs and to developing new and innovative security solutions that redefine the security landscape.

Industry/Entity Type

Internet

Font styles to use
Serif
Sans Serif
Script

Colors
0792cd
33a6d7
85cae6

```html
<!DOCTYPE html>
<html lang="en">
<head>
<meta charset="utf-8">
<title>Velbrantix Business Card</title>
<link rel="stylesheet" href="https://fonts.googleapis.com/css2?family=Nunito:wght@700;800&family=Open+Sans:wght@400;600&display=swap">
<style>
  :root {
    --brand-deep: #0792cd;
    --brand-mid: #33a6d7;
    --brand-light: #85cae6;
    --card-top: #a9dcf1;
    --card-bottom: #1f8fc6;
    --ink-light: #e9f7fd;
    --ink-dark: #1b7fb4;
    --page: #eef3f6;
  }
  * { margin: 0; padding: 0; box-sizing: border-box; }
  html, body { width: 1200px; height: 950px; overflow: hidden; background: var(--page); }
  .sheet {
    position: relative; width: 1200px; height: 950px;
    display: flex; flex-direction: column; align-items: center; justify-content: center; gap: 50px;
  }
  .card {
    position: relative; width: 700px; height: 400px; border-radius: 4px; overflow: hidden;
    box-shadow: 0 10px 28px rgba(20, 60, 90, 0.22);
  }
  .card-back {
    background: linear-gradient(135deg, var(--card-top) 0%, var(--brand-light) 55%, #6fa9c4 100%);
  }
  .card-front { background: linear-gradient(180deg, var(--card-top) 0%, #9bd5ee 50%); }
  .waves { position: absolute; inset: 0; width: 100%; height: 100%; }
  .brand-mark { display: flex; align-items: center; gap: 14px; }
  .brand-dot { border-radius: 50%; background: var(--brand-deep); }
  .brand-name {
    font-family: "Nunito", sans-serif; font-weight: 800; color: var(--brand-deep); letter-spacing: 0.5px;
  }
  .card-back .brand-mark { position: absolute; left: 50%; top: 130px; transform: translateX(-50%); }
  .card-back .brand-dot { width: 92px; height: 92px; }
  .card-back .brand-name { font-size: 46px; }
  .card-back .site {
    position: absolute; left: 0; right: 0; top: 258px; text-align: center;
    font-family: "Open Sans", sans-serif; font-size: 17px; letter-spacing: 4px; color: #2a79a3;
  }
  .card-front .brand-mark { position: absolute; left: 56px; top: 70px; }
  .card-front .brand-dot { width: 58px; height: 58px; }
  .card-front .brand-name { font-size: 36px; }
  .person { position: absolute; right: 52px; top: 118px; text-align: right; font-family: "Nunito", sans-serif; font-weight: 800; color: var(--brand-deep); }
  .person-name { font-size: 24px; letter-spacing: 1px; }
  .person-role { font-size: 15px; letter-spacing: 1px; }
  .address {
    position: absolute; left: 40px; top: 268px; font-family: "Open Sans", sans-serif;
    font-size: 19px; line-height: 1.3; color: var(--ink-light);
  }
  .contacts {
    position: absolute; right: 40px; top: 250px; list-style: none;
    font-family: "Open Sans", sans-serif; font-size: 18px; color: var(--ink-light);
  }
  .contacts li { display: flex; justify-content: flex-end; align-items: center; gap: 10px; height: 27px; }
  .contacts svg { width: 18px; height: 18px; fill: var(--ink-light); }
</style>
</head>
<body>
<main class="sheet">
  <section class="card card-back" aria-label="Card back">
    <div class="brand-mark"><span class="brand-dot"></span><span class="brand-name">Velbrantix</span></div>
    <p class="site">www.velbrantix.net</p>
  </section>

  <section class="card card-front" aria-label="Card front">
    <svg class="waves" viewBox="0 0 700 400" preserveAspectRatio="none" aria-hidden="true">
      <defs>
        <linearGradient id="deepFill" x1="0" y1="0" x2="0" y2="1">
          <stop offset="0" stop-color="#33a6d7"/>
          <stop offset="1" stop-color="#0a85bf"/>
        </linearGradient>
      </defs>
      <path d="M0 160 C 150 175, 230 230, 400 218 S 620 195, 700 205 L700 400 L0 400 Z" fill="#5cb8e0"/>
      <path d="M0 175 C 150 200, 230 245, 400 232 S 620 210, 700 218 L700 400 L0 400 Z" fill="#ffffff" opacity="0.85"/>
      <path d="M0 185 C 160 212, 240 255, 400 242 S 620 220, 700 226 L700 400 L0 400 Z" fill="url(#deepFill)"/>
      <path d="M0 200 C 160 230, 260 262, 420 250 S 620 232, 700 238" stroke="#0792cd" stroke-width="6" fill="none" opacity="0.7"/>
    </svg>

    <div class="brand-mark"><span class="brand-dot"></span><span class="brand-name">Velbrantix</span></div>

    <div class="person">
      <p class="person-name">MARA TOLVEK</p>
      <p class="person-role">PRESIDENT</p>
    </div>

    <address class="address">2417 Harrowgate Lane<br>Brookvale, NY 11290</address>

    <ul class="contacts">
      <li>555 0142 7781
        <svg viewBox="0 0 20 20"><path d="M3 8 Q10 2 17 8 L15 10 L13 8 L7 8 L5 10 Z M5 11 H15 V17 H5 Z"/></svg></li>
      <li>555 0198 3364
        <svg viewBox="0 0 20 20"><path d="M6 3 H14 V8 H6 Z M3 9 H17 V16 H3 Z"/></svg></li>
      <li>mara@velbrantix.net
        <svg viewBox="0 0 20 20"><path d="M2 5 H18 V15 H2 Z M2 5 L10 11 L18 5" stroke="#1f8fc6" stroke-width="1.2"/></svg></li>
      <li>www.velbrantix.net
        <svg viewBox="0 0 20 20"><circle cx="10" cy="10" r="8"/><path d="M2 10 H18 M10 2 V18" stroke="#1f8fc6" stroke-width="1.2"/></svg></li>
    </ul>
  </section>
</main>
</body>
</html>
```